Hardcore nerd needs to stand out in a sea of dull Defence business cards

Wombarra Devices is a new Australian consulting engineering company that turns research and theory into practical systems. No evangelistic fluff, just mathematics and physics into electronic and optical circuits for consumer products, scientific research or Defence applications.

We already have a recognised logo (provided) which is often dark blue/black on a light background but we're open to other combinations. (Us engineers tend to have limited aesthetic imagination :)

Some of our recent products have included:
* Instrumentation for electrical testing,
* Radar jammers,
* GPS antenna design,
* Satellite tracking systems,
* High power lasers

We're open to both single and double-sided designs - happy to be convinced either way.

P.S. Another group is working on the web page, so - alas - our web site is currently of no use for images/ideas...

Target Market(s)

Engineering managers,
Scientists

Contact Information for Business Card

Dr Colin Harte
R&D Engineer

colin@wombarradevices.com.au
0427 563 710

PO Box XXX (to be confirmed)
Kelsby ACT 2917
Australia

Font styles to use
Serif
Sans Serif

Colors

Designer to choose colors to be used in the design.

Requirements
Must have
• My contact details!
• I've had many (great) "bold and plain" designs submitted already, so feel free to be artistically creative :)
• Happy to take advice re fonts/colours/printability etc.
Nice to have
• I'm not sure if "lists" are more at home on a CV than a business card, but representative services include:
• Applied electromagnetics
• RF and high speed electronics
• Signal and image processing
• Electro-optical and laser systems
• Concept-to-prototype design services
• If you're considering double sided cards, then often measuring/alignment grids/rulers feature on the back of similar cards.
• e.g. https://www.veltranoptics.example/newgrouppage9.cfm?objectgroup_id=4183
• https://www.veltranoptics.example/newgrouppage9.cfm?objectgroup_ID=4185
• ..or even a "Smith chart" (google will return lots)
• Generic images to represent a capability might work - googling images associated with keyword for each of these areas might help:
• - "passive radar", "phased array", "fdtd", "vircator"
• RF and high speed electronic design
• - "smith chart", "microstrip circuits", "dimensioned drawing", "electronic schematic"
• - "dft", "iir filter"
• - "optical cavity". "laser energy level diagram"
• Background/watermarked images outlines/wireframes/schematics would probably look OK.
Should not have
• If a list of projects/services is provided, it is important not to make the client feel that this is "all" the company can do. Engineering design is a creative discipline (like graphics :)
• Please, no stock "military" snaps like planes, missiles, etc!

```html
<!DOCTYPE html>
<html lang="en">
<head>
<meta charset="utf-8">
<title>Wombarra Devices – Business Card</title>
<link rel="stylesheet" href="https://fonts.googleapis.com/css2?family=Lato:wght@400;700;900&display=swap">
<style>
  :root {
    --backdrop: #626160;
    --navy: #03205f;
    --paper: #ffffff;
    --ink: #1c1c1c;
  }
  * { margin: 0; padding: 0; box-sizing: border-box; }
  html, body {
    width: 1064px;
    height: 1200px;
    overflow: hidden;
    background: var(--backdrop);
    font-family: "Lato", Arial, sans-serif;
  }
  .canvas { position: relative; width: 1064px; height: 1200px; }

  .card {
    position: absolute;
    width: 630px;
    height: 390px;
  }
  .card--front {
    left: 265px;
    top: 141px;
    background: var(--paper);
    border-radius: 0 195px 195px 0;
  }
  .card--back {
    left: 233px;
    top: 584px;
    background: var(--navy);
    border-radius: 195px 0 0 195px;
  }

  .holder {
    position: absolute;
    left: 30px;
    top: 50px;
    line-height: 1;
  }
  .holder__name {
    font-weight: 900;
    font-size: 21px;
    letter-spacing: 0.2px;
    color: var(--navy);
  }
  .holder__role {
    margin-top: 3px;
    font-size: 17px;
    color: var(--ink);
  }

  .address {
    position: absolute;
    left: 32px;
    top: 206px;
    font-size: 17px;
    line-height: 23px;
    color: var(--ink);
  }

  .contacts {
    position: absolute;
    left: 30px;
    top: 273px;
    list-style: none;
    font-size: 17px;
    line-height: 23px;
    color: var(--ink);
  }
  .contacts li { display: flex; align-items: center; }
  .contacts svg { width: 13px; height: 13px; margin-right: 8px; fill: var(--navy); flex: none; }

  .brand-front {
    position: absolute;
    left: 370px;
    top: 92px;
    width: 200px;
    display: flex;
    flex-direction: column;
    align-items: center;
  }
  .brand-front__dot {
    width: 150px;
    height: 150px;
    border-radius: 50%;
    background: var(--navy);
  }
  .brand-front__name {
    margin-top: 14px;
    font-weight: 900;
    font-size: 15px;
    letter-spacing: 1.5px;
    color: var(--navy);
    text-transform: uppercase;
  }

  .brand-back {
    position: absolute;
    left: 145px;
    top: 133px;
    display: flex;
    align-items: center;
    gap: 14px;
  }
  .brand-back__dot {
    width: 116px;
    height: 116px;
    border-radius: 50%;
    background: var(--paper);
  }
  .brand-back__name {
    color: var(--paper);
    font-weight: 900;
    text-transform: uppercase;
    line-height: 1;
  }
  .brand-back__name span { display: block; }
  .brand-back__line1 { font-size: 37px; letter-spacing: 0.5px; }
  .brand-back__line2 { font-size: 22px; letter-spacing: 5px; margin-top: 4px; }
</style>
</head>
<body>
<main class="canvas">

  <section class="card card--front" aria-label="Card front">
    <div class="holder">
      <p class="holder__name">DR COLIN HARTE</p>
      <p class="holder__role">R&amp;D Engineer</p>
    </div>

    <address class="address" style="font-style:normal">
      PO Box XXX<br>
      Kelsby ACT 2917, Australia
    </address>

    <ul class="contacts">
      <li>
        <svg viewBox="0 0 16 16" aria-hidden="true"><path d="M1 5c0-2 3-3 7-3s7 1 7 3v1.5h-3.5V5h-7v1.5H1zM3 8l2-2h6l2 2v6H3zm5 1.2a2 2 0 100 4 2 2 0 000-4z"/></svg>
        0427 563 710
      </li>
      <li>
        <svg viewBox="0 0 16 16" aria-hidden="true"><path d="M1 3h14v1.2L8 9 1 4.2zM1 5.8l7 4.8 7-4.8V13H1z"/></svg>
        colin@wombarradevices.com.au
      </li>
      <li>
        <svg viewBox="0 0 16 16" aria-hidden="true"><circle cx="8" cy="8" r="7"/><path d="M5 4c1 1 3 1 3 3s-2 1-2 3 1 2 1 4M10 3c0 2 2 2 3 3M11 10c1 0 2 1 2 2" stroke="#fff" stroke-width="1.2" fill="none"/></svg>
        www.wombarradevices.com.au
      </li>
    </ul>

    <div class="brand-front">
      <div class="brand-front__dot" aria-hidden="true"></div>
      <p class="brand-front__name">Wombarra Devices</p>
    </div>
  </section>

  <section class="card card--back" aria-label="Card back">
    <div class="brand-back">
      <div class="brand-back__dot" aria-hidden="true"></div>
      <p class="brand-back__name">
        <span class="brand-back__line1">Wombarra</span>
        <span class="brand-back__line2">Devices</span>
      </p>
    </div>
  </section>

</main>
</body>
</html>
```